Clear Harbor Business card

We are a company that owns 2 compliance software programs for TV, Radio and Cable industries as well as an online job board. We need a professional business card that incorproates all three logos.

```html
<!DOCTYPE html>
<html lang="en">
<head>
<meta charset="utf-8">
<title>Clear Harbor – Business Card</title>
<link rel="stylesheet" href="https://fonts.googleapis.com/css2?family=Roboto:wght@400;700&family=Roboto+Condensed:wght@400;700&display=swap">
<style>
  :root{
    --bg:#2a2b30;
    --card:#ffffff;
    --navy:#2b2a6b;
    --red:#e8402a;
    --blue:#1e7bc4;
  }
  *{box-sizing:border-box;margin:0;padding:0}
  html,body{width:1200px;height:800px;overflow:hidden}
  body{background:var(--bg);font-family:"Roboto",Arial,sans-serif;position:relative}
  .card{
    position:absolute;left:320px;width:560px;height:320px;
    background:var(--card);box-shadow:0 12px 30px rgba(0,0,0,.45);overflow:hidden;
  }
  .card--front{top:48px}
  .card--back{top:432px}
  .brand-row{
    position:absolute;left:0;right:0;padding:0 24px;
    display:flex;align-items:center;justify-content:center;gap:14px;
  }
  .card--front .brand-row{top:136px}
  .card--back .brand-row{top:78px}
  .brand{display:flex;align-items:center;gap:6px;font-weight:700;font-size:16px;color:var(--navy);white-space:nowrap}
  .brand__dot{width:10px;height:10px;border-radius:50%;background:var(--navy);flex:none}
  .brand--jobs{color:var(--blue)}
  .brand--jobs .brand__dot{background:var(--blue)}
  .divider{width:2px;height:44px;background:var(--navy);flex:none}
  .holder{
    position:absolute;left:48px;top:196px;display:flex;align-items:center;gap:24px;
  }
  .holder__id{text-align:right}
  .holder__name{font-family:"Roboto Condensed",Arial,sans-serif;font-weight:700;font-size:30px;color:var(--navy);letter-spacing:.5px;line-height:1}
  .holder__role{font-family:"Roboto Condensed",Arial,sans-serif;font-size:17px;color:var(--red);margin-top:4px}
  .holder__rule{width:2px;height:62px;background:var(--navy)}
  .contact{list-style:none;font-size:15px;color:var(--navy);line-height:1.45}
  .contact li{display:flex;align-items:center;gap:8px;white-space:nowrap}
  .contact svg{width:12px;height:12px;flex:none}
  .stripe{position:absolute;bottom:0;height:9px}
  .stripe--navy{left:0;width:55%;background:var(--navy)}
  .stripe--red{right:0;width:45%;background:var(--red);height:11px}
</style>
</head>
<body>
  <section class="card card--front" aria-label="Card front">
    <div class="brand-row">
      <div class="brand"><span class="brand__dot"></span>AirCheck Suite</div>
      <span class="divider"></span>
      <div class="brand"><span class="brand__dot"></span>LineCheck Suite</div>
      <span class="divider"></span>
      <div class="brand brand--jobs"><span class="brand__dot"></span>StageWork Jobs</div>
    </div>
  </section>

  <section class="card card--back" aria-label="Card back">
    <div class="brand-row">
      <div class="brand"><span class="brand__dot"></span>AirCheck Suite</div>
      <span class="divider"></span>
      <div class="brand"><span class="brand__dot"></span>LineCheck Suite</div>
      <span class="divider"></span>
      <div class="brand brand--jobs"><span class="brand__dot"></span>StageWork Jobs</div>
    </div>

    <div class="holder">
      <div class="holder__id">
        <p class="holder__name">DANA REYES</p>
        <p class="holder__role">Director</p>
      </div>
      <span class="holder__rule"></span>
      <ul class="contact">
        <li><svg viewBox="0 0 12 12"><rect x="2.5" y="1" width="7" height="10" rx="1" fill="none" stroke="#e8402a" stroke-width="1.4"/></svg>(555) 014 2870</li>
        <li><svg viewBox="0 0 12 12"><rect x="1" y="2.5" width="10" height="7" fill="#e8402a"/><path d="M1 2.5 6 7l5-4.5" fill="none" stroke="#fff" stroke-width="1"/></svg>info@clearharbor.example</li>
        <li><svg viewBox="0 0 12 12"><circle cx="6" cy="6" r="5" fill="#e8402a"/><path d="M1 6h10M6 1c-2.5 3-2.5 7 0 10M6 1c2.5 3 2.5 7 0 10" fill="none" stroke="#fff" stroke-width=".8"/></svg>www.clearharbor.example</li>
      </ul>
    </div>

    <span class="stripe stripe--navy"></span>
    <span class="stripe stripe--red"></span>
  </section>
</body>
</html>
```